Refresh of far from plain IT company website

Our web site is starting to show it's age. You can see the existing site here: www.plumbwick.net. As a growing company we want to come across as a dynamic collection of IT experts.

We want to update the design so are open to any colour palette and look, but want to retain our current table logo. We use the logo on our business cards but with a white background - see the attached file, so you don't need to keep the brown or the green.

The design should consider the range of browsers that will be looking at the site - so please show how it will look on a wide screen laptop and a 768x1024 tablet.

We want to add some pages about our team and their skills, probably with photos of each person on the team.

This is an uncoded project - the PSD files of the design is required, not coding.
Updates

Thanks everyone for the submissions so far.  It's a holiday day in the UK today but we will get some feedback on the designs so far out to you.

Target Market(s)

Architects and other creative types looking for IT support

Industry/Entity Type

Business

Font styles to use
Serif
Sans Serif

Requirements
Must have
• Must look good on a laptop and an iPad.

```html
<!DOCTYPE html>
<html lang="en">
<head>
<meta charset="utf-8">
<title>Plumbwick – IT Support Management</title>
<link href="https://fonts.googleapis.com/css2?family=Open+Sans:wght@400;600;700&display=swap" rel="stylesheet">
<style>
:root{
  --magenta:#a8145f;
  --magenta-dark:#8e0f50;
  --gold:#d8aa00;
  --ink:#3a3a3a;
  --muted:#555;
  --panel:#f2f2f2;
  --rule:#e2e2e2;
  --footer:#454545;
  --footer-base:#3a3a3a;
  --footer-text:#d6d6d6;
}
*{box-sizing:border-box;margin:0;padding:0}
html,body{width:953px;height:1200px;overflow:hidden;background:#fff}
body{position:relative;font-family:"Open Sans",Arial,sans-serif;color:var(--ink)}
.abs{position:absolute}
a{color:inherit;text-decoration:none}

/* header */
.brand{left:110px;top:27px;display:flex;align-items:center;gap:10px}
.brand-mark{width:20px;height:20px;background:var(--gold)}
.brand-name{font-size:27px;font-weight:600;color:var(--magenta);letter-spacing:-.3px}
.remote{left:625px;top:31px;display:flex;align-items:center;height:28px}
.remote label{font-size:11px;color:#222;margin-right:14px}
.remote .field{width:127px;height:28px;border:1px solid #d4d4d4;background:#f7f7f7;font-size:10px;color:#aaa;padding:0 10px;line-height:26px}
.remote .go{width:34px;height:28px;background:var(--gold);margin-left:9px;display:flex;align-items:center;justify-content:center}

/* nav */
.nav{left:0;top:82px;width:953px;height:42px;background:linear-gradient(#b3186a,var(--magenta-dark))}
.nav a{position:absolute;top:15px;font-size:11.5px;font-weight:600;color:#fff;letter-spacing:.2px}
.nav a.current{color:var(--gold)}

/* hero */
.hero{left:0;top:124px;width:953px;height:352px;overflow:hidden}
.hero-photo{position:absolute;inset:0;background:linear-gradient(90deg,#f4f6f8 0%,#e3e8ee 30%,#c3cbd6 55%,#8e9bb0 75%,#4a4e57 90%,#2d2f34 100%)}
.hero h1{position:absolute;left:99px;top:84px;font-size:28px;font-weight:400;color:var(--magenta);letter-spacing:.3px}
.hero ul{position:absolute;left:103px;top:128px;list-style:none}
.hero li{font-size:14.5px;color:#222;height:24px;display:flex;align-items:center;gap:10px}
.btn-gold{position:absolute;left:103px;top:263px;width:111px;height:30px;background:var(--gold);color:#fff;font-size:13.5px;font-weight:600;display:flex;align-items:center;justify-content:center}
.dots{position:absolute;left:444px;top:321px;display:flex;gap:8px}
.dots span{width:10px;height:10px;border-radius:50%;background:#fff}
.dots span.on{background:#222}

/* section headings */
.h2{font-size:19px;font-weight:400;color:#555}
.h2 em{font-style:normal;color:var(--magenta)}
.arrows{font-size:15px;font-weight:700;color:#333;letter-spacing:3px}

.welcome-text{left:103px;top:538px;width:238px;font-size:10.5px;line-height:18.4px;color:var(--muted)}
.btn-dark{left:103px;top:702px;width:80px;height:28px;background:#3a3a3a;color:var(--gold);font-size:11px;display:flex;align-items:center;justify-content:center}

.service{top:543px;width:150px;height:187px;background:var(--panel);text-align:center}
.service svg{margin-top:16px}
.service h3{font-size:15px;font-weight:600;color:var(--magenta);margin-top:6px}
.service p{font-size:10.6px;line-height:16px;color:var(--muted);margin-top:5px;padding:0 10px}
.service .more{display:block;font-size:10.6px;color:var(--magenta);margin-top:5px}

.rule-h{left:103px;top:752px;width:747px;height:1px;background:var(--rule)}
.rule-v{left:469px;top:770px;width:1px;height:222px;background:var(--rule)}

.post{top:802px;width:163px}
.post .thumb{width:160px;height:82px;border:1px solid #ddd}
.post h4{font-size:11.5px;font-weight:400;line-height:15.5px;color:var(--magenta);margin-top:11px}
.post p{font-size:11px;line-height:15.5px;color:var(--muted);margin-top:4px}
.post .read{display:block;font-size:10px;font-weight:700;color:#222;margin-top:6px}

.strip{left:483px;width:367px;height:70px;background:var(--panel);display:flex;align-items:center;justify-content:space-around;padding:0 8px}
.strip span{font-size:15px;font-weight:600;color:#6a6a6a;display:flex;align-items:center;gap:6px}
.strip i{display:inline-block;width:14px;height:14px;background:#7a7a7a}

/* footer */
.footer{left:0;top:1023px;width:953px;height:133px;background:var(--footer)}
.footer h5{position:absolute;top:22px;font-size:13px;font-weight:600;color:#fff}
.footer ul{position:absolute;top:50px;list-style:none}
.footer li{font-size:10px;color:var(--footer-text);height:20.7px}
.footer .accent{color:#e0609f}
.footer dl{position:absolute;left:639px;top:48px;font-size:10px;color:var(--footer-text)}
.footer dl div{display:flex;height:18.5px}
.footer dt{width:57px}
.base{left:0;top:1156px;width:953px;height:44px;background:var(--footer-base)}
.base p{position:absolute;left:103px;top:15px;font-size:10px;color:var(--footer-text)}
.social{position:absolute;top:10px;width:26px;height:26px;border-radius:50%;background:#2e80c9}
</style>
</head>
<body>

<header>
  <div class="abs brand"><span class="brand-mark"></span><span class="brand-name">plumbwick</span></div>
  <form class="abs remote">
    <label>Remote:</label>
    <div class="field">Session ID:</div>
    <div class="go"><svg width="12" height="14" viewBox="0 0 12 14"><path d="M3 2l6 5-6 5" fill="none" stroke="#fff" stroke-width="3"/></svg></div>
  </form>
</header>

<nav class="abs nav">
  <a class="current" style="left:102px">HOME</a>
  <a style="left:168px">ABOUT US</a>
  <a style="left:257px">WHAT WE DO</a>
  <a style="left:364px">NEWS BLOG</a>
  <a style="left:463px">ARTICLES</a>
  <a style="left:546px">CLIENTS</a>
  <a style="left:623px">PARTNERS</a>
  <a style="left:713px">SUPPORT</a>
  <a style="left:797px">CONTACT</a>
</nav>

<section class="abs hero">
  <div class="hero-photo" role="img" aria-label="Photo of an IT engineer standing beside a server rack, with colleagues in a bright office behind"></div>
  <h1>IT SUPPORT MANAGEMENT</h1>
  <ul>
    <li><svg width="13" height="11" viewBox="0 0 13 11"><path d="M1 6l4 4 7-9" fill="none" stroke="var(--magenta)" stroke-width="2.5"/></svg>Client/Server Network</li>
    <li><svg width="13" height="11" viewBox="0 0 13 11"><path d="M1 6l4 4 7-9" fill="none" stroke="var(--magenta)" stroke-width="2.5"/></svg>Cabling and Wireless Solution</li>
    <li><svg width="13" height="11" viewBox="0 0 13 11"><path d="M1 6l4 4 7-9" fill="none" stroke="var(--magenta)" stroke-width="2.5"/></svg>Data and Voice Convergence</li>
    <li><svg width="13" height="11" viewBox="0 0 13 11"><path d="M1 6l4 4 7-9" fill="none" stroke="var(--magenta)" stroke-width="2.5"/></svg>Security &amp; Penetration Testing</li>
    <li><svg width="13" height="11" viewBox="0 0 13 11"><path d="M1 6l4 4 7-9" fill="none" stroke="var(--magenta)" stroke-width="2.5"/></svg>Multi-site Connectivity</li>
  </ul>
  <a class="btn-gold">Read More</a>
  <div class="dots"><span class="on"></span><span></span><span></span><span></span></div>
</section>

<section>
  <h2 class="abs h2" style="left:103px;top:503px">Welcome to <em>Plumbwick</em></h2>
  <p class="abs welcome-text">Plumbwick was established with a specific aim: to consistently deliver an advanced and comprehensive IT service for ambitious growing companies across many industry sectors. We aim to provide the very best in service and support, and to aid business growth through the effective and skilled use of modern IT solutions.</p>
  <a class="abs btn-dark">Read More</a>
</section>

<section>
  <h2 class="abs h2" style="left:368px;top:503px">What we do at <em>Plumbwick</em></h2>
  <div class="abs arrows" style="left:831px;top:508px">‹›</div>

  <article class="abs service" style="left:368px">
    <svg width="56" height="56" viewBox="0 0 56 56"><path d="M44 14A22 22 0 1 0 50 30" fill="none" stroke="#666" stroke-width="5"/><path d="M40 6l8 8-10 3z" fill="#666"/><text x="28" y="33" font-family="Open Sans,sans-serif" font-size="14" font-weight="700" fill="#666" text-anchor="middle">24/7</text></svg>
    <h3>Support</h3>
    <p>Plumbwick's clients enjoy regular scheduled on-site visits from an engineer.</p>
    <a class="more">More &gt;&gt;</a>
  </article>
  <article class="abs service" style="left:534px">
    <svg width="66" height="56" viewBox="0 0 66 56"><g fill="#666"><circle cx="33" cy="16" r="8"/><path d="M19 50c0-14 6-22 14-22s14 8 14 22z"/><circle cx="14" cy="24" r="6"/><path d="M2 50c0-11 5-17 12-17 3 0 5 1 7 3-2 4-3 9-3 14z"/><circle cx="52" cy="24" r="6"/><path d="M64 50c0-11-5-17-12-17-3 0-5 1-7 3 2 4 3 9 3 14z"/></g></svg>
    <h3>Consultancy</h3>
    <p>Plumbwick's clients enjoy regular scheduled on-site visits from an engineer.</p>
    <a class="more">More &gt;&gt;</a>
  </article>
  <article class="abs service" style="left:700px">
    <svg width="60" height="56" viewBox="0 0 60 56"><g fill="#666"><path d="M18 26a8 8 0 0 1 4-15 11 11 0 0 1 21 2 7 7 0 0 1 1 13z"/><rect x="6" y="30" width="48" height="22" rx="8"/></g><circle cx="44" cy="41" r="3" fill="#f2f2f2"/></svg>
    <h3>Hosting</h3>
    <p>Plumbwick's clients enjoy regular scheduled on-site visits from an engineer.</p>
    <a class="more">More &gt;&gt;</a>
  </article>
</section>

<div class="abs rule-h"></div>
<div class="abs rule-v"></div>

<section>
  <h2 class="abs h2" style="left:103px;top:765px">News <em>Blog</em></h2>
  <article class="abs post" style="left:103px">
    <div class="thumb" role="img" aria-label="Illustration of two mobile platform mascots side by side" style="background:linear-gradient(90deg,#dfe3e8 0%,#b9c0c8 45%,#b6d35a 55%,#9cc23c 100%)"></div>
    <h4>Plumbwick Pomme and Robota App launched..</h4>
    <p>Plumbwick have released Pomme and Robota apps that allow customers...</p>
    <a class="read">Read More</a>
  </article>
  <article class="abs post" style="left:294px">
    <div class="thumb" role="img" aria-label="Photo of a hand touching a stream of binary data" style="background:linear-gradient(90deg,#1d3b52 0%,#3f7392 55%,#6fa3bd 100%)"></div>
    <h4>CoreLattice Certified Installa-tion Engineers..</h4>
    <p>Plumbwick are resellers of CoreLattice's StorNote and StorChorus products...</p>
    <a class="read">Read More</a>
  </article>
</section>

<section>
  <h2 class="abs h2" style="left:483px;top:765px">Our <em>Partners</em></h2>
  <div class="abs arrows" style="left:831px;top:772px">‹›</div>
  <div class="abs strip" style="top:802px">
    <span><i></i>Boxvault</span><span>Ardena</span><span><i style="border-radius:50%"></i>Mailwell</span>
  </div>
  <h2 class="abs h2" style="left:483px;top:885px">Our <em>Clients</em></h2>
  <div class="abs arrows" style="left:831px;top:893px">‹›</div>
  <div class="abs strip" style="top:922px">
    <span>Harlow Pike</span><span>KRVN</span><span>Quintile</span>
  </div>
</section>

<footer class="abs footer">
  <h5 style="left:103px">Quick Links</h5>
  <ul style="left:103px"><li>Home</li><li>About us</li><li>What we do</li><li>News blog</li></ul>
  <ul style="left:189px"><li>Articles</li><li>Clients</li><li>Partners</li></ul>
  <h5 style="left:293px">Help</h5>
  <ul style="left:293px"><li>Contact</li><li>Support</li><li>Terms</li></ul>
  <h5 style="left:437px">Contact Info</h5>
  <ul style="left:437px;top:50px"><li class="accent" style="height:15.5px">Plumbwick.net Ltd</li><li style="height:15.5px">Fenwick House</li><li style="height:15.5px">48-52 Mercer Lane, London EC2X 9QT</li><li style="height:15.5px">United Kingdom</li></ul>
  <h5 style="left:639px">Contact Us</h5>
  <dl>
    <div><dt>Tel:</dt><dd>020 7946 0181</dd></div>
    <div><dt>Fax:</dt><dd>020 7946 0182</dd></div>
    <div><dt>Email:</dt><dd class="accent">website@plumbwick.net</dd></div>
  </dl>
</footer>

<div class="abs base">
  <p>Copyright © 2014. Plumbwick.net.Ltd. All Right Reserved</p>
  <span class="social" style="left:767px;background:#3b5a9a"></span>
  <span class="social" style="left:795px;background:#2d9fd9"></span>
  <span class="social" style="left:824px;background:#1f78b4"></span>
</div>

</body>
</html>
```